Business Card Design

Hi I need a business card designed, we already have the business name logo artwork and would like some concept ideas for the Bus Card layout.
On the back of the card i want to include the products and services that we offer.
We are a Plastics Sheeting manufacture based in Perth Australia.

                                       

We need a BC design for a company called Tarvo Plastics based in Perth Australia.

We supply from DIY to Trade & Industrial  Engineering Markets.

We specialise in:

·         Cut to size panels  (all shapes and sizes)

·         Plastics fabrication & Welding

·         Custom Designs

·         Plastic Repairs

·         PVC Pipe Slotting & PVC Pipe Threading

·         Supplier of all types of engineering plastics and profiles.

Including:           Acrylic / Clarvene

                               Polycarbonate / Dorvil

                               Prismatic Light Diffuser

                               Vantrib

                               HDPE / UHMWPE

                               PVC / PVC Foam

                               Nylon

                               HIPS

```html
<!DOCTYPE html>
<html lang="en">
<head>
<meta charset="utf-8">
<title>Tarvo Plastics – Business Card</title>
<link rel="stylesheet" href="https://fonts.googleapis.com/css2?family=Open+Sans:wght@400;600;700;800&display=swap">
<style>
  :root {
    --navy: #1d2b5c;
    --orange: #f39a1e;
    --sky: #2b9ad3;
    --ink: #4a4f5c;
    --white: #ffffff;
    --stage: #e9eaee;
  }
  * { box-sizing: border-box; margin: 0; padding: 0; }
  html, body {
    width: 1200px; height: 720px; overflow: hidden;
    background: var(--stage);
    font-family: "Open Sans", Arial, sans-serif;
  }
  .canvas {
    position: relative; width: 1200px; height: 720px;
    display: flex; align-items: center; justify-content: center; gap: 32px;
  }
  .card {
    position: relative; width: 560px; height: 342px; overflow: hidden;
    box-shadow: 0 6px 18px rgba(20, 30, 60, .18);
  }

  /* Front */
  .card-front { background: var(--white); }
  .front-wave { position: absolute; inset: 0; width: 100%; height: 100%; }
  .brand {
    display: flex; align-items: center; gap: 10px;
    font-weight: 800; line-height: 1; letter-spacing: -0.5px;
  }
  .brand-mark { width: 18px; height: 18px; background: var(--orange); flex: none; }
  .card-front .brand { position: absolute; left: 54px; top: 32px; color: var(--navy); font-size: 44px; }
  .contact-block { position: absolute; left: 0; top: 108px; width: 100%; display: flex; }
  .identity { width: 272px; text-align: right; padding-right: 14px; color: var(--ink); font-size: 12.5px; line-height: 1.35; }
  .person-name { color: var(--navy); font-weight: 700; font-size: 16px; }
  .person-title { color: var(--orange); font-size: 11.5px; font-weight: 600; margin-bottom: 6px; }
  .address + .address { margin-top: 5px; }
  .divider { width: 1px; height: 118px; background: #b9bcc6; }
  .contact-details { padding-left: 14px; }
  .contacts { color: var(--ink); font-size: 12px; line-height: 1.45; list-style: none; }
  .contacts li { display: flex; align-items: center; gap: 6px; }
  .contacts svg { width: 11px; height: 11px; flex: none; }
  .entity { margin-top: 5px; font-size: 12px; line-height: 1.35; color: var(--ink); }

  /* Back */
  .card-back { background: var(--navy); color: var(--white); padding: 28px 30px 0; }
  .card-back .brand { justify-content: center; font-size: 44px; color: var(--white); }
  .tagline { margin-top: 16px; text-align: center; font-weight: 700; font-size: 14px; line-height: 1.35; }
  .offer { display: flex; margin-top: 14px; }
  .offer-col h2 { color: var(--orange); font-size: 16px; font-weight: 700; margin-bottom: 4px; }
  .offer-col ul { list-style: none; font-size: 12.5px; line-height: 1.42; }
  .offer-col li { position: relative; padding-left: 13px; }
  .offer-col li::before {
    content: ""; position: absolute; left: 0; top: 7px;
    width: 6px; height: 6px; border-radius: 50%; background: var(--orange);
  }
  .services { width: 290px; }
  .offer-divider { width: 1px; height: 150px; background: rgba(255,255,255,.45); margin: 4px 20px 0 8px; }
  .materials { flex: 1; }
</style>
</head>
<body>
<main class="canvas">

  <section class="card card-front" aria-label="Business card front">
    <svg class="front-wave" viewBox="0 0 560 342" preserveAspectRatio="none" aria-hidden="true">
      <path d="M0,324 C180,306 380,276 560,266 L560,342 L0,342 Z" fill="#1d2b5c"/>
      <path d="M0,310 C180,292 380,260 560,248" fill="none" stroke="#2b9ad3" stroke-width="5"/>
    </svg>

    <div class="brand"><span class="brand-mark"></span>Tarvo Plastics</div>

    <div class="contact-block">
      <div class="identity">
        <p class="person-name">Your Name</p>
        <p class="person-title">Title</p>
        <p class="address">Unit 4/18 Brenmore Circuit<br>Kelvale WA 6155</p>
        <p class="address">PO Box 2284<br>Kelvale DC WA 6970</p>
      </div>
      <div class="divider"></div>
      <div class="contact-details">
        <ul class="contacts">
          <li><svg viewBox="0 0 12 12"><circle cx="6" cy="6" r="6" fill="#f39a1e"/><path d="M4 3.2l1 1.6-.6.6c.4.9 1 1.5 1.9 1.9l.6-.6 1.6 1-.5 1.1C5.8 8.7 3.3 6.2 3 4z" fill="#fff"/></svg>08 9410 3370</li>
          <li><svg viewBox="0 0 12 12"><rect x="3" y="1" width="6" height="10" rx="1.2" fill="#f39a1e"/><rect x="4.2" y="2.4" width="3.6" height="5.6" fill="#fff"/></svg>0400 218 655</li>
          <li><svg viewBox="0 0 12 12"><rect x="1" y="4" width="10" height="6" rx="1" fill="#f39a1e"/><rect x="3" y="1.5" width="6" height="3" fill="#f39a1e"/><rect x="3.5" y="6" width="5" height="2" fill="#fff"/></svg>08 9410 3371</li>
          <li><svg viewBox="0 0 12 12"><rect x="1" y="2.5" width="10" height="7" rx="1" fill="#f39a1e"/><path d="M1.5 3l4.5 3.5L10.5 3" fill="none" stroke="#fff" stroke-width="1"/></svg>sales@tarvoplastics.com.au</li>
        </ul>
        <p class="entity">Tarvo Holdings Pty Ltd<br>T/A Tarvo Plastics ABN: TBA</p>
      </div>
    </div>
  </section>

  <section class="card card-back" aria-label="Business card back">
    <div class="brand">Tarvo Plastics</div>
    <p class="tagline">The Products And Services That We Offer<br>Are Supplied From Diy To Trade &amp; Industrial Engineering Markets</p>

    <div class="offer">
      <div class="offer-col services">
        <h2>We specialise in:</h2>
        <ul>
          <li>Cut to size panels (all shapes and sizes)</li>
          <li>Plastics fabrication &amp; Welding</li>
          <li>Custom Designs</li>
          <li>Plastic Repairs</li>
          <li>PVC Pipe Slotting &amp; PVC Pipe Threading</li>
          <li>Supplier of all types of engineering plastics and profiles</li>
        </ul>
      </div>
      <div class="offer-divider"></div>
      <div class="offer-col materials">
        <h2>Including:</h2>
        <ul>
          <li>Acrylic / Clarvene</li>
          <li>Polycarbonate / Dorvil</li>
          <li>Prismatic Light Diffuser</li>
          <li>Vantrib &nbsp;• HDPE / UHMWPE</li>
          <li>PVC / PVC Foam</li>
          <li>Nylon &nbsp;• HIPS</li>
        </ul>
      </div>
    </div>
  </section>

</main>
</body>
</html>
```